KT Morrow Insurance Group, LLC - Branding Project

We have an existing business card that was designed on Plume Press. We recently completed a new logo design with sketch hive and would like to utilize this new logo design into a business card design. Our new logo will be a major emphasis of our branding that is currently under development.

We are an independent insurance agency licensed in Colorado. We specialized in four keys areas. Business Insurance, Risk Management, Employee Benefits and Investments.

We would like the efforts of this design to last for 5 years minimum. Existing business card and new logo design files attached.

Industry/Entity Type

Business

Contact Information for Business Card

See attached files for existing business card design.

Requirements
Must have
• My office is a virtual office. All of our marketing effort drive from the Denver, CO office location. Our mailing address is just for mailing, that's it.
• Please maintain the color scheme of the new logo design.
Nice to have
• Doublesided card, I think? Your the expert if you have other ideas that are better I am excited to see them.

```html
<!DOCTYPE html>
<html lang="en">
<head>
<meta charset="utf-8">
<title>KT Morrow Insurance Group – Stationery</title>
<link href="https://fonts.googleapis.com/css2?family=Questrial&display=swap" rel="stylesheet">
<style>
:root{
  --bg:#cbcbcb;
  --purple:#38307e;
  --blue:#1d9ad6;
  --paper:#f3f3f3;
  --ink:#4a4a4a;
  --muted:#8a8a8a;
  --sig:#dfe3ef;
}
*{box-sizing:border-box;margin:0;padding:0}
html,body{width:1200px;height:1000px;overflow:hidden}
body{background:var(--bg);font-family:"Questrial",sans-serif;color:var(--ink);position:relative}
.piece{position:absolute}

/* brand lockup */
.brand{display:flex;align-items:center;gap:8px;color:var(--blue)}
.brand-dot{border-radius:50%;background:var(--blue);flex:none}
.brand-name{line-height:1.05;color:var(--blue)}
.brand-name span{display:block}
.brand-rule{align-self:stretch;width:1px;background:var(--blue);flex:none}

/* folder */
.folder{left:152px;top:41px;width:431px;height:559px;background:var(--purple);border-radius:3px}
.folder-spine{position:absolute;left:20px;top:0;bottom:0;width:6px;border-left:1px solid rgba(255,255,255,.12);border-right:1px solid rgba(255,255,255,.12)}
.folder .brand{position:absolute;left:150px;top:70px}
.folder .brand-dot{width:50px;height:50px}
.folder .brand-rule{height:68px}
.folder .brand-name{font-size:22px}
.folder .brand-name span+span{font-size:13px;letter-spacing:1px}

/* letterhead */
.letterhead{left:615px;top:61px;width:418px;height:539px;background:var(--paper)}
.letterhead .brand{position:absolute;left:40px;top:36px}
.letterhead .brand-dot{width:30px;height:30px}
.letterhead .brand-rule{height:46px}
.letterhead .brand-name{font-size:14px}
.letterhead .brand-name span+span{font-size:8px;letter-spacing:.6px}
.letter-body{position:absolute;left:38px;top:180px;width:342px;font-size:6.2px;line-height:1.45;text-align:justify;color:var(--ink)}
.letter-body p{margin-bottom:6px}
.letter-body .salute{font-weight:bold;margin-bottom:8px}
.signoff{display:flex;align-items:center;gap:16px;margin-top:10px}
.signoff-text strong{display:block}
.signature{width:84px;height:30px;background:var(--sig);border-radius:2px;flex:none}
.letter-foot{position:absolute;left:28px;right:28px;bottom:18px;display:flex;font-size:6px;line-height:1.5;color:var(--ink)}
.letter-foot div{padding:0 8px;border-left:1px solid #bbb}
.letter-foot div:first-child{border-left:0;padding-left:0}
.icon{display:inline-block;width:6px;height:6px;background:var(--blue);border-radius:1px;margin-right:3px;vertical-align:-1px}

/* band */
.band{position:absolute;left:0;right:0;bottom:0;height:7px;display:flex;gap:2px}
.band i{display:block;height:100%}
.band .p{background:var(--purple)}
.band .b{background:var(--blue)}

/* envelope front */
.envelope{left:117px;top:630px;width:468px;height:202px;background:var(--paper)}
.envelope .brand{position:absolute;left:22px;top:20px}
.envelope .brand-dot{width:40px;height:40px}
.envelope .brand-rule{height:46px}
.envelope .brand-name{font-size:15px}
.envelope .brand-name span+span{font-size:8.5px;letter-spacing:.6px}
.return-address{position:absolute;left:22px;top:167px;font-size:6.2px;line-height:1.5}

/* envelope back */
.envelope-back{left:616px;top:630px;width:416px;height:202px;background:var(--paper)}
.envelope-back svg{position:absolute;left:0;top:0}

/* cards */
.card{top:862px;width:176px;height:98px}
.card-front{left:410px;background:var(--purple)}
.card-front .brand{position:absolute;left:12px;top:16px}
.card-front .brand-dot{width:20px;height:20px}
.card-front .brand-rule{height:24px}
.card-front .brand-name{font-size:9.5px}
.card-front .brand-name span+span{font-size:5px;letter-spacing:.4px}
.card-url{position:absolute;left:12px;bottom:10px;font-size:4.5px;color:#fff}
.card-back{left:616px;background:var(--paper)}
.card-back .brand{position:absolute;left:86px;top:12px}
.card-back .brand-dot{width:18px;height:18px}
.card-back .brand-rule{height:22px}
.card-back .brand-name{font-size:8.5px}
.card-back .brand-name span+span{font-size:4.5px;letter-spacing:.4px}
.card-person{position:absolute;left:8px;top:16px;font-size:5px;line-height:1.3}
.card-person strong{display:block;color:var(--purple)}
.card-contact{position:absolute;left:8px;top:62px;font-size:4.2px;line-height:1.55}
.card-contact .icon{width:4px;height:4px;margin-right:2px}
.card-address{position:absolute;right:8px;top:62px;font-size:4.2px;line-height:1.45;text-align:right}
.card .band{height:4px;gap:1px}
</style>
</head>
<body>

<section class="piece folder" aria-label="Presentation folder">
  <div class="folder-spine"></div>
  <div class="brand">
    <div class="brand-dot" style="background:#fff"></div>
    <div class="brand-rule"></div>
    <div class="brand-name" style="color:#fff"><span>KT Morrow</span><span>Insurance Group</span></div>
  </div>
</section>

<section class="piece letterhead" aria-label="Letterhead">
  <div class="brand">
    <div class="brand-dot"></div>
    <div class="brand-rule"></div>
    <div class="brand-name"><span>KT Morrow</span><span>Insurance Group</span></div>
  </div>
  <div class="letter-body">
    <p class="salute">Dear sir,</p>
    <p>Thank you for trusting our agency with your coverage needs. We review every policy with care and explain each option in plain terms so you can decide with confidence. Our team works across business insurance, risk management, employee benefits and investments.</p>
    <p>This letter confirms that your renewal documents are ready for review. Please read the enclosed summary, note any changes to your limits or deductibles, and contact your account executive with questions before the renewal date shown on page one.</p>
    <p>We value a long working relationship and will reach out each year to confirm your needs are still met.</p>
    <p>Thank you again for your business. We look forward to serving you.</p>
    <div class="signoff">
      <div class="signoff-text">Yours Sincerely,<strong>Lena Varga</strong></div>
      <div class="signature" role="img" aria-label="Handwritten signature"></div>
    </div>
  </div>
  <div class="letter-foot">
    <div>22 Larch Plaza, 1180 Elm Street<br>Suite 210, Denver, CO 80204</div>
    <div><span class="icon"></span>555.010.4821<br><span class="icon"></span>555.010.4827</div>
    <div><span class="icon"></span>info@ktmorrowins.example<br><span class="icon"></span>www.ktmorrowins.example</div>
    <div>PO Box 417<br>Fairview, CO 80999</div>
  </div>
  <div class="band"><i class="p" style="width:32%"></i><i class="b" style="width:44%"></i><i class="p" style="flex:1"></i></div>
</section>

<section class="piece envelope" aria-label="Envelope front">
  <div class="brand">
    <div class="brand-dot"></div>
    <div class="brand-rule"></div>
    <div class="brand-name"><span>KT Morrow</span><span>Insurance Group</span></div>
  </div>
  <p class="return-address">PO Box 417<br>Fairview, CO 80999</p>
  <div class="band"><i class="p" style="width:70%"></i><i class="b" style="flex:1"></i></div>
</section>

<section class="piece envelope-back" aria-label="Envelope back">
  <svg width="416" height="202" viewBox="0 0 416 202" aria-hidden="true">
    <path d="M0 0H416L404 62Q402 70 394 70H22Q14 70 12 62Z" fill="var(--purple)"/>
    <circle cx="208" cy="32" r="12" fill="var(--blue)"/>
  </svg>
</section>

<section class="piece card card-front" aria-label="Business card front">
  <div class="brand">
    <div class="brand-dot" style="background:#fff"></div>
    <div class="brand-rule"></div>
    <div class="brand-name" style="color:#fff"><span>KT Morrow</span><span>Insurance Group</span></div>
  </div>
  <p class="card-url">www.ktmorrowins.example</p>
</section>

<section class="piece card card-back" aria-label="Business card back">
  <p class="card-person"><strong>DANA MORROW</strong>Account Executive</p>
  <div class="brand">
    <div class="brand-dot"></div>
    <div class="brand-rule"></div>
    <div class="brand-name"><span>KT Morrow</span><span>Insurance Group</span></div>
  </div>
  <p class="card-contact"><span class="icon"></span>555.010.4820<br><span class="icon"></span>555.010.4821<br><span class="icon"></span>dana@ktmorrowins.example<br><span class="icon"></span>www.ktmorrowins.example</p>
  <p class="card-address">22 Larch Plaza, 1180 Elm Street<br>Suite 210, Denver, CO 80204<br>Post Office Box 5120<br>Harlow, Alabama 36990</p>
  <div class="band"><i class="p" style="width:50%"></i><i class="b" style="flex:1"></i></div>
</section>

</body>
</html>
```